Business Card for Vorla Parts Wholesale supplier

Hi There! I need a new business card for our company. We are specialized in selling Vorla parts, mostly we sell new LCD screens for Zelnar and Drelks. I would like to see that back in the design.

You can find the colors and logo's on our website: www.hartuvo.nl

Industry/Entity Type

Business

Contact Information for Business Card

My Details:
Tobias Lindqvist

Phone: 0031687203316
E-mail: Tobias@hartuvo.nl

Slogan: "Because Quality Matters"

Font styles to use
Sans Serif

Colors

Designer to choose colors to be used in the design.

Requirements
Must have
• A Black backside with the Hartuvo logo on it. The front side should be clean with only my contact details.
• But I'm also open for something really different or awesome!
Nice to have
• Remember that we are in the parts & repairing industry, So i'll be handing those business cards mainly to repair companies. Maybe you can do something with that thought :)

```html
<!DOCTYPE html>
<html lang="en">
<head>
<meta charset="utf-8">
<title>Hartuvo Business Card</title>
<link href="https://fonts.googleapis.com/css2?family=Saira:wght@500;600&family=Open+Sans:wght@400;600&display=swap" rel="stylesheet">
<style>
  :root {
    --backdrop: #5b4a3a;
    --card-white: #ffffff;
    --card-black: #000000;
    --brand-orange: #f37321;
    --ink: #111111;
    --ink-soft: #555555;
    --rule: #9a9a9a;
    --faint-mark: #1b120b;
  }
  * { margin: 0; padding: 0; box-sizing: border-box; }
  html, body { width: 1200px; height: 987px; overflow: hidden; }
  body { background: var(--backdrop); position: relative; font-family: "Open Sans", sans-serif; }

  .card { position: absolute; width: 615px; height: 352px; box-shadow: 0 2px 6px rgba(0,0,0,0.35); overflow: hidden; }
  .card-front { left: 293px; top: 130px; background: var(--card-white); }
  .card-back { left: 292px; top: 505px; background: var(--card-black); }

  .brand { position: absolute; display: flex; align-items: center; gap: 12px; }
  .brand-front { left: 46px; top: 52px; }
  .brand-dot { width: 52px; height: 52px; border-radius: 50%; background: var(--brand-orange); }
  .brand-name { font-family: "Saira", sans-serif; font-weight: 600; line-height: 1; }
  .brand-front .brand-name { font-size: 54px; color: var(--ink); }

  .holder-name { position: absolute; right: 45px; top: 188px; font-family: "Saira", sans-serif; font-weight: 600; font-size: 23px; color: var(--brand-orange); letter-spacing: 0.5px; }
  .divider { position: absolute; left: 46px; width: 524px; top: 229px; height: 1px; background: var(--rule); }

  .contact { position: absolute; left: 46px; display: flex; align-items: center; gap: 8px; color: var(--ink-soft); }
  .contact-phone { top: 242px; font-size: 16px; font-family: "Saira", sans-serif; }
  .contact-mail { top: 267px; font-size: 14px; }
  .contact svg { width: 15px; height: 15px; fill: var(--brand-orange); flex: none; }

  .web-band { position: absolute; left: 0; right: 0; top: 307px; height: 32px; background: var(--card-black); }
  .web-band-orange { position: absolute; left: 0; top: 0; bottom: 0; width: 498px; background: var(--brand-orange); }
  .web-url { position: absolute; left: 47px; top: 6px; font-size: 14px; color: var(--card-white); letter-spacing: 4px; }
  .band-dot { position: absolute; left: 482px; top: 0; width: 32px; height: 32px; border-radius: 50%; background: var(--card-white); }

  .back-mark { position: absolute; left: 10px; top: 0; width: 346px; height: 346px; border-radius: 50%; background: var(--faint-mark); }
  .back-brand { position: absolute; left: 375px; top: 248px; }
  .back-brand .brand-name { font-size: 56px; color: var(--card-white); }
  .slogan { position: absolute; left: 375px; top: 309px; font-size: 16.5px; font-weight: 600; color: var(--card-white); }
</style>
</head>
<body>
  <section class="card card-front">
    <div class="brand brand-front">
      <span class="brand-dot"></span>
      <span class="brand-name">hartuvo</span>
    </div>
    <div class="holder-name">Tobias Lindqvist</div>
    <div class="divider"></div>
    <div class="contact contact-phone">
      <svg viewBox="0 0 24 24" aria-hidden="true"><path d="M6.6 10.8a15.1 15.1 0 0 0 6.6 6.6l2.2-2.2a1 1 0 0 1 1-.25 11.4 11.4 0 0 0 3.6.6 1 1 0 0 1 1 1V20a1 1 0 0 1-1 1A17 17 0 0 1 3 4a1 1 0 0 1 1-1h3.5a1 1 0 0 1 1 1c0 1.25.2 2.45.6 3.6a1 1 0 0 1-.25 1z"/></svg>
      <span>0031687203316</span>
    </div>
    <div class="contact contact-mail">
      <svg viewBox="0 0 24 24" aria-hidden="true"><path d="M2 5h20v14H2z M3 6l9 7 9-7" fill="var(--brand-orange)" stroke="#fff" stroke-width="1.5"/></svg>
      <span>Tobias@hartuvo.nl</span>
    </div>
    <div class="web-band">
      <div class="web-band-orange"></div>
      <span class="web-url">www.hartuvo.nl</span>
      <span class="band-dot"></span>
    </div>
  </section>

  <section class="card card-back">
    <div class="back-mark"></div>
    <div class="brand back-brand">
      <span class="brand-name">hartuvo</span>
    </div>
    <div class="slogan">Because Quality Matters</div>
  </section>
</body>
</html>
```